Print on top the name of the company: (Or Similar)
Lumora Cleaning & Disinfecting
Because your standards aren't standard.

We adhere to ALL QRV guidelines for both residential and commercial cleaning.

Infection Control is our ultimate goal.

Instructions:
Opening a residential and commercial cleaning and disinfecting company in south Florida.

Targeting high-end residential clients, commercial and healthcare facilities, specializing in Ambulatory Care Guidelines. With a concentration and expertise in targeting Covid 19 and other transmissible pathogens.

WELM trained.
Owned and operated by a licensed BSN Registered Nurse specially ​trained in Infection Control Prevention with over 25 years experience. Over two decades in Ambulatory Surgery Center Administration, Director of Nursing and Infection Control Prevention ad Consulting.

Looking to create a business flier that emphasizes Cleaning & Disinfection
along with the standard expectation for residential and Commercial cleaning services

Target Market(s)

Residential & Commercial

Font styles to use
Decorative

Requirements
Must have
• A checklist for cleaning services

```html
<!DOCTYPE html>
<html lang="en">
<head>
<meta charset="utf-8">
<title>Gleamwell Cleaning Flyer</title>
<link href="https://fonts.googleapis.com/css2?family=Raleway:wght@400;500;600;700;800;900&display=swap" rel="stylesheet">
<style>
  :root {
    --backdrop: #a3a4a8;
    --paper: #ffffff;
    --paper-shade: #e4e5e7;
    --brand-blue: #0a73c1;
    --brand-yellow: #f4ee22;
    --ink: #2f3033;
    --photo-sky: #bfe2f0;
    --photo-warm: #e9d46a;
    --footer: #5b5b5e;
    --footer-ink: #ffffff;
    --rule-grey: #7a7a7d;
  }
  * { margin: 0; padding: 0; box-sizing: border-box; }
  html, body { width: 906px; height: 1200px; overflow: hidden; }
  body {
    background: var(--backdrop);
    font-family: "Raleway", sans-serif;
    color: var(--ink);
    position: relative;
  }
  .flyer {
    position: absolute;
    left: 29px; top: 0;
    width: 848px; height: 1200px;
    background: linear-gradient(90deg, var(--paper-shade) 0%, var(--paper) 38%);
    overflow: hidden;
  }
  .flyer-shapes {
    position: absolute; left: 0; top: 0;
    width: 848px; height: 1200px;
  }
  .title {
    position: absolute; left: 47px; top: 93px;
    font-weight: 900; font-size: 70px; line-height: 74px;
    color: var(--brand-blue); letter-spacing: -0.5px;
    text-transform: uppercase;
  }
  .tagline, .promise {
    position: absolute; left: 49px;
    font-weight: 600; font-size: 25px; line-height: 33.6px;
    color: var(--ink);
  }
  .tagline { top: 265px; width: 362px; }
  .promise { top: 417px; width: 340px; }
  .tagline-rule {
    position: absolute; left: 49px; top: 391px;
    width: 357px; height: 3px; background: var(--brand-blue);
  }
  .goal {
    position: absolute; left: 49px; top: 673px;
    font-weight: 800; font-size: 28.5px; line-height: 34px;
    color: var(--brand-blue); letter-spacing: -0.4px;
    text-transform: uppercase; white-space: nowrap;
  }
  .about-col {
    position: absolute; top: 756px;
    text-align: center; color: var(--ink);
  }
  .about-col--brief { left: 60px; width: 206px; top: 758px; font-size: 19.5px; line-height: 24px; font-weight: 500; }
  .about-col--focus { left: 302px; width: 196px; font-size: 13.6px; line-height: 17.1px; font-weight: 500; }
  .about-col--owner { left: 540px; width: 244px; font-size: 13.6px; line-height: 17.1px; font-weight: 500; }
  .about-divider {
    position: absolute; top: 755px; width: 1.5px; height: 180px;
    background: var(--rule-grey);
  }
  .about-divider--first { left: 283px; }
  .about-divider--second { left: 520px; }
  .footer {
    position: absolute; left: 0; top: 964px;
    width: 848px; height: 211px;
    background: var(--footer); color: var(--footer-ink);
  }
  .service-list { position: absolute; top: 18px; }
  .service-list--commercial { left: 58px; }
  .service-list--residential { left: 263px; }
  .service-list h2 {
    font-weight: 800; font-size: 18.5px; line-height: 28px;
    text-transform: uppercase; letter-spacing: 0.2px;
    border-left: 2px solid var(--footer-ink);
    padding-left: 6px; margin-bottom: 5px;
  }
  .service-list ul { list-style: none; }
  .service-list li { font-size: 13.6px; line-height: 17.1px; font-weight: 500; white-space: nowrap; }
  .call-out {
    position: absolute; left: 470px; top: 39px; width: 354px;
    text-align: center;
  }
  .call-out p { font-weight: 800; font-size: 23.5px; line-height: 28.6px; }
  .call-out .phone { font-weight: 800; font-size: 36px; line-height: 40px; margin-top: 8px; letter-spacing: 0.5px; }
  .footer-strip {
    position: absolute; left: 0; top: 1175px; width: 848px; height: 25px;
    background: var(--paper);
  }
</style>
</head>
<body>
<main class="flyer">
  <svg class="flyer-shapes" viewBox="0 0 1188 1681" preserveAspectRatio="none">
    <defs>
      <linearGradient id="photoTone" x1="0" y1="0" x2="1" y2="1">
        <stop offset="0" stop-color="#bfe2f0"/>
        <stop offset="0.55" stop-color="#cfe6ee"/>
        <stop offset="1" stop-color="#e9d46a"/>
      </linearGradient>
    </defs>
    <path role="img" aria-label="Photo of cleaning supplies: spray bottle, brushes, sponge and yellow gloves in a wooden crate"
          d="M760 58 L994 0 H1188 V885 C1000 830 800 805 606 806 L606 690 L700 125 Q712 70 760 58 Z"
          fill="url(#photoTone)"/>
    <path d="M520 812 C800 792 1050 838 1188 880 V955 C1050 880 800 818 520 822 Z" fill="#f4ee22"/>
    <path d="M0 918 H920 C1000 930 1080 970 1128 1016 H0 Z" fill="#f4ee22"/>
    <path d="M520 826 C800 812 1050 875 1188 950 V1008 C1060 905 800 842 520 832 Z" fill="#0a73c1"/>
  </svg>

  <h1 class="title">Gleamwell<br>Cleaning</h1>
  <p class="tagline">Lumora Cleaning &amp; Disinfecting Because your standards aren't standard.</p>
  <div class="tagline-rule"></div>
  <p class="promise">We adhere to ALL QRV guidelines for both residential and commercial cleaning.</p>

  <p class="goal">Infection control is our ultimate goal.</p>

  <p class="about-col about-col--brief">INSTRUCTIONS:<br>Opening a residential and commercial cleaning and disinfecting company in south Florida.</p>
  <div class="about-divider about-divider--first"></div>
  <p class="about-col about-col--focus">Targeting high-end residential clients, commercial and healthcare facilities, specializing in Ambulatory Care Guidelines. With a concentration and expertise in targeting Covid 19 and other transmissible pathogens.</p>
  <div class="about-divider about-divider--second"></div>
  <p class="about-col about-col--owner">WELM TRAINED.<br>Owned and operated by a licensed BSN Registered Nurse specially trained in Infection Control Prevention with over 25 years experience. Over two decades in Ambulatory Surgery Center Administration, Director of Nursing and Infection Control Prevention ad Consulting.</p>

  <footer class="footer">
    <section class="service-list service-list--commercial">
      <h2>Commercial</h2>
      <ul>
        <li>Janitorial</li><li>Offices</li><li>Floor Maintenance</li><li>Carpet Cleaning</li>
        <li>Move-ins</li><li>Move-outs</li><li>Construction Clean-ups</li><li>Estate Clean-outs</li>
      </ul>
    </section>
    <section class="service-list service-list--residential">
      <h2>Residential</h2>
      <ul>
        <li>House cleaning</li><li>Before and after party</li><li>Move-ins</li><li>Move-outs</li>
        <li>Holiday cleaning</li><li>Seasonal cleaning</li><li>Carpet cleaning</li><li>Deodorizing and sanitizing</li>
      </ul>
    </section>
    <div class="call-out">
      <p>Call us to find out<br>how you can save money<br>this month!</p>
      <p class="phone">(555) 010 24 68</p>
    </div>
  </footer>
  <div class="footer-strip"></div>
</main>
</body>
</html>
```